Business Card for a Dental Office

The design should communicate integrity, quality and reliability. We also want the card look elegant, simple, but still stand out, different from the traditional-dental-office business card.

Industry/Entity Type

Business

```html
<!DOCTYPE html>
<html lang="en">
<head>
<meta charset="utf-8">
<title>Marlow Dental Studio – Business Card</title>
<link href="https://fonts.googleapis.com/css2?family=Bebas+Neue&family=Source+Sans+3:wght@400;600;700&display=swap" rel="stylesheet">
<style>
  :root {
    --stage: #000000;
    --paper: #ffffff;
    --ink: #111111;
    --gold: #c9a91f;
    --gold-deep: #a88a12;
    --gold-top: #c5a82e;
    --gold-mid: #dcc52f;
    --gold-bottom: #cbae2b;
  }
  * { margin: 0; padding: 0; box-sizing: border-box; }
  html, body {
    width: 1200px; height: 900px; overflow: hidden;
    background: var(--stage);
  }
  .canvas { position: relative; width: 1200px; height: 900px; }

  .card { position: absolute; top: 275px; width: 477px; height: 293px; overflow: hidden; }
  .card--front {
    left: 116px; background: var(--paper);
    border-radius: 0 52px 0 52px;
    font-family: "Source Sans 3", Arial, sans-serif; color: var(--ink);
  }
  .card--back {
    left: 622px; top: 276px; height: 292px;
    border-radius: 56px 0 56px 0;
    background: linear-gradient(180deg, var(--gold-top) 0%, var(--gold-mid) 55%, var(--gold-bottom) 100%);
  }

  .holder { position: absolute; right: 19px; top: 33px; text-align: right; }
  .holder__name { font-size: 20px; font-weight: 600; color: var(--gold); line-height: 1; }
  .holder__role { font-size: 13px; margin-top: 5px; line-height: 1; }

  .brand { position: absolute; left: 25px; top: 78px; display: flex; align-items: flex-end; gap: 8px; }
  .brand__mark { width: 58px; height: 58px; background: var(--ink); }
  .brand__text { padding-bottom: 0; }
  .brand__name {
    font-family: "Bebas Neue", Impact, sans-serif;
    font-size: 27px; line-height: 0.9; color: var(--ink); letter-spacing: 0.2px;
  }
  .brand__tagline {
    font-size: 10.5px; font-weight: 600; color: var(--gold-deep);
    letter-spacing: 0.4px; text-transform: uppercase; line-height: 1; margin-top: 2px;
  }

  .address { position: absolute; right: 21px; top: 158px; text-align: right; font-size: 13px; line-height: 17px; }

  .contacts { position: absolute; right: 19px; top: 217px; list-style: none; font-size: 13px; line-height: 18px; }
  .contacts li { display: flex; justify-content: flex-end; align-items: center; gap: 7px; }
  .contacts svg { width: 10px; height: 10px; fill: var(--gold); }

  .back__emblem {
    position: absolute; left: 52px; top: 0; width: 374px; height: 215px;
    background: radial-gradient(ellipse at 50% 60%, rgba(255,240,120,0.18), rgba(255,240,120,0) 70%);
  }
  .back__brand { position: absolute; left: 0; right: 0; top: 222px; text-align: center; }
  .back__name {
    font-family: "Bebas Neue", Impact, sans-serif;
    font-size: 40px; line-height: 0.9; color: var(--ink);
  }
  .back__tagline {
    font-family: "Source Sans 3", Arial, sans-serif;
    font-size: 14.5px; font-weight: 700; color: var(--ink);
    text-transform: uppercase; letter-spacing: 0.6px; line-height: 1; margin-top: 2px;
  }
</style>
</head>
<body>
<main class="canvas">
  <section class="card card--front" aria-label="Business card front">
    <div class="holder">
      <p class="holder__name">Daniel Hartley</p>
      <p class="holder__role">Managing Director</p>
    </div>

    <div class="brand">
      <span class="brand__mark" aria-hidden="true"></span>
      <div class="brand__text">
        <p class="brand__name">Marlow Dental Studio</p>
        <p class="brand__tagline">Your smile is your gift to others</p>
      </div>
    </div>

    <address class="address" style="font-style:normal">
      12345, Address Goes Here<br>Country Name, 123456
    </address>

    <ul class="contacts">
      <li>044-123 456 789
        <svg viewBox="0 0 10 10" aria-hidden="true"><path d="M2 0.5 L3.6 2.6 L2.8 3.6 C3.5 5 5 6.5 6.4 7.2 L7.4 6.4 L9.5 8 L8.4 9.5 C4.5 9.2 0.8 5.5 0.5 1.6 Z"/></svg>
      </li>
      <li>info@webname.com
        <svg viewBox="0 0 10 10" aria-hidden="true"><path d="M0.5 2 H9.5 V8.5 H0.5 Z M1.2 2.6 L5 5.4 L8.8 2.6" stroke="#fff" stroke-width="0.7"/></svg>
      </li>
      <li>www.websitename.com
        <svg viewBox="0 0 10 10" aria-hidden="true"><path d="M4 6 L6 4" stroke="#c9a91f" stroke-width="1.2" fill="none"/><path d="M3.6 4.4 L1.8 6.2 A1.4 1.4 0 0 0 3.8 8.2 L5.6 6.4 M6.4 5.6 L8.2 3.8 A1.4 1.4 0 0 0 6.2 1.8 L4.4 3.6" stroke="#c9a91f" stroke-width="1.2" fill="none"/></svg>
      </li>
    </ul>
  </section>

  <section class="card card--back" aria-label="Business card back">
    <div class="back__emblem" role="img" aria-label="Faint brand emblem in lighter gold"></div>
    <div class="back__brand">
      <p class="back__name">Marlow Dental Studio</p>
      <p class="back__tagline">Your smile is your gift to others</p>
    </div>
  </section>
</main>
</body>
</html>
```